business card

Business card for new business.
Red and black corporate colors.
Card can have an Indsutrial feel to it. Feel free to add Rust, Bolted steel, or graphics as you see fit. We provide highly specialized services to the below mentioned industries.
Keep information out of corners so that if I want I can choose rounded corners.
Information
- front. name - title - phone - email
- Rear
Pipelines - Marine - Fabrication - Forestry - Utility
Halden - Ironvale - Port Ashcombe - Brennanford - Westmoor

```html
<!DOCTYPE html>
<html lang="en">
<head>
<meta charset="utf-8">
<title>Girderline Business Card</title>
<link href="https://fonts.googleapis.com/css2?family=Roboto+Condensed:wght@700&family=Roboto:wght@400;500&display=swap" rel="stylesheet">
<style>
  :root {
    --stage: #e9e7e4;
    --card-white: #f3f3f3;
    --card-black: #1b1c1e;
    --brand-red: #e30613;
    --brand-grey: #6d6e70;
    --text-dark: #4a4a4a;
    --text-light: #f2f2f2;
    --rule: #c9c9c9;
  }
  * { margin: 0; padding: 0; box-sizing: border-box; }
  html, body { width: 1200px; height: 960px; overflow: hidden; }
  body { background: var(--stage); position: relative; font-family: "Roboto", Arial, sans-serif; }

  .card { position: absolute; width: 600px; height: 343px; box-shadow: 0 2px 6px rgba(0,0,0,.25); }

  .card-front { left: 314px; top: 113px; background: var(--card-white); }
  .brand { position: absolute; left: 62px; top: 133px; height: 58px; display: flex; align-items: center; gap: 12px; }
  .brand-square { width: 22px; height: 22px; background: var(--brand-red); }
  .brand-name { font-family: "Roboto Condensed", Arial, sans-serif; font-weight: 700; font-size: 42px; color: var(--brand-grey); letter-spacing: 0.5px; }
  .divider { position: absolute; left: 337px; top: 102px; width: 1px; height: 118px; background: var(--rule); }
  .contact { position: absolute; left: 361px; top: 113px; }
  .person-name { font-family: "Roboto Condensed", Arial, sans-serif; font-weight: 700; font-size: 23px; color: var(--brand-red); line-height: 1.1; }
  .person-title { font-size: 15px; color: var(--brand-grey); margin-top: 3px; letter-spacing: 0.3px; }
  .contact-line { display: flex; align-items: center; gap: 10px; font-size: 15px; color: var(--text-dark); margin-top: 3px; }
  .contact-line:first-of-type { margin-top: 12px; }
  .contact-line svg { width: 14px; height: 14px; fill: var(--brand-red); flex: none; }
  .web-band { position: absolute; left: 0; top: 280px; width: 100%; height: 34px; background: var(--brand-red); color: #fff; font-size: 14px; letter-spacing: 6px; text-align: center; line-height: 34px; }

  .card-back { left: 311px; top: 472px; height: 342px; background: var(--card-black); }
  .back-mark { position: absolute; left: 258px; top: 80px; width: 84px; height: 145px; background: var(--brand-red); }
  .services { position: absolute; left: 0; top: 255px; width: 100%; text-align: center; color: var(--text-light); font-size: 15px; line-height: 18px; }
  .sep { display: inline-block; width: 4px; height: 4px; background: var(--brand-red); vertical-align: middle; margin: 0 4px; }
</style>
</head>
<body>
  <section class="card card-front">
    <div class="brand">
      <span class="brand-square"></span>
      <span class="brand-name">GIRDERLINE</span>
    </div>
    <div class="divider"></div>
    <div class="contact">
      <p class="person-name">MARK HOLLAND</p>
      <p class="person-title">CEO/FOUNDER</p>
      <p class="contact-line">
        <svg viewBox="0 0 24 24" aria-hidden="true"><path d="M6.6 10.8a15 15 0 0 0 6.6 6.6l2.2-2.2c.3-.3.7-.4 1-.2 1.1.4 2.3.6 3.6.6.6 0 1 .4 1 1V20c0 .6-.4 1-1 1A17 17 0 0 1 3 4c0-.6.4-1 1-1h3.5c.6 0 1 .4 1 1 0 1.3.2 2.5.6 3.6.1.3 0 .7-.2 1z"/></svg>
        587 214 9063
      </p>
      <p class="contact-line">
        <svg viewBox="0 0 24 24" aria-hidden="true"><path d="M2 5h20v14H2z"/><path d="M3 6l9 7 9-7" fill="none" stroke="#f3f3f3" stroke-width="1.6"/></svg>
        info@girderline.com
      </p>
    </div>
    <div class="web-band">www.girderline.com</div>
  </section>

  <section class="card card-back">
    <div class="back-mark"></div>
    <div class="services">
      <p>Pipelines<span class="sep"></span>Marine<span class="sep"></span>Fabrication<span class="sep"></span>Forestry</p>
      <p>Utility<span class="sep"></span>Halden<span class="sep"></span>Ironvale<span class="sep"></span>Port Ashcombe</p>
      <p>Brennanford<span class="sep"></span>Westmoor</p>
    </div>
  </section>
</body>
</html>
```